Tallow Reed Software

We are a software company selling endpoint visibility, access and security technology to enterprise-level IT departments.

Our technology helps organizations gain comprehensive visibility into and control over devices accessing their corporate network so they can quickly identify and address suspicious activity on the network that could lead to potential threats like data breaches.

This technology can cost organizations upwards of $1M - depending on the size of the organization. Our primary clients are Pinnacle 2,000 companies.

We want a professional, polished business card to represent our new brand.

Info fields to include on the card:
Name
Job Title
Office Phone #
Cell Phone #
Email address
Address: 4270 Vestridge Pond Blvd., Ste. 2600, Larkfield, WI 55812
Website address: www.tallowreedsoftware.example
Tagline: See every device. Secure the network.

Logo files and color specs document are attached. Would like color scheme to coordinate with the logo.

Also looking at stationary/envelope designs in conjunction with the business card designs. Received very few designs that included the stationary.

Software

```html
<!DOCTYPE html>
<html lang="en">
<head>
<meta charset="utf-8">
<title>Tallow Reed Software — Stationery System</title>
<link rel="stylesheet" href="https://fonts.googleapis.com/css2?family=Montserrat:wght@500;600&family=Open+Sans:ital,wght@0,400;0,600;1,400&display=swap">
<style>
:root{
  --brand-red:#8b2429;
  --accent:#c4673c;
  --paper:#f4f4f3;
  --card-white:#f7f7f6;
  --ink:#4a4a4a;
  --ink-soft:#8a8a8a;
  --backdrop:#cdcdcd;
}
*{box-sizing:border-box;margin:0;padding:0}
html,body{width:1200px;height:1000px;overflow:hidden}
body{background:var(--backdrop);font-family:"Open Sans",Arial,sans-serif;color:var(--ink);position:relative}
.piece{position:absolute}

/* brand lockup */
.lockup{display:flex;align-items:center;gap:8px;font-family:"Montserrat",Arial,sans-serif;font-weight:600;text-transform:uppercase;letter-spacing:.12em;line-height:1.15;white-space:nowrap}
.lockup .mark{flex:none;background:currentColor}
.lockup--white{color:#fff}
.lockup--red{color:var(--brand-red)}

.tagline{font-style:italic;color:#fff;white-space:nowrap}

/* folder */
.folder{left:83px;top:268px;width:340px;height:455px;background:var(--brand-red)}
.folder .lockup{position:absolute;left:84px;top:80px;font-size:16px}
.folder .lockup .mark{width:20px;height:20px}
.folder .mark-small{position:absolute;left:261px;top:403px;width:12px;height:12px;background:#fff;opacity:.85}
.folder .tagline{position:absolute;right:26px;top:428px;font-size:6.5px}

/* letterhead */
.letterhead{left:452px;top:282px;width:313px;height:441px;background:var(--paper)}
.letterhead .lockup{position:absolute;left:47px;top:28px;font-size:9px;gap:6px}
.letterhead .lockup .mark{width:10px;height:10px}
.letter-body{position:absolute;left:46px;top:112px;width:224px;font-size:5.2px;line-height:9.3px;color:var(--ink)}
.letter-body p{margin-bottom:9px}
.signature{position:absolute;left:194px;top:338px;width:70px;height:12px;background:linear-gradient(90deg,rgba(74,74,74,.18),rgba(74,74,74,.05));border-radius:6px}

/* contact footer */
.footer{position:absolute;display:flex;justify-content:space-between;color:var(--ink-soft);white-space:nowrap}
.footer .col{flex:none;border-left:.6px solid #bbb;padding-left:5px}
.footer .col:first-child{border-left:none;padding-left:0}
.footer b{color:var(--accent);font-weight:600}
.letterhead .footer{left:46px;right:46px;bottom:12px;font-size:3.5px;line-height:5.5px}
.envelope-front .footer{left:55px;right:22px;bottom:15px;font-size:3.6px;line-height:5.2px}

/* business cards */
.card{width:126px;height:82px}
.card-front{left:811px;top:256px;background:var(--brand-red)}
.card-front .lockup{position:absolute;left:34px;top:30px;font-size:6px;gap:4px}
.card-front .lockup .mark{width:7px;height:7px}
.card-front .tagline{position:absolute;left:47px;top:48px;font-size:3.6px}
.card-back{left:990px;top:256px;background:var(--card-white)}
.card-back .lockup{position:absolute;right:10px;top:11px;font-size:5.2px;gap:4px}
.card-back .lockup .mark{width:6px;height:6px}
.card-name{position:absolute;left:10px;top:34px;font-size:7.5px;color:var(--ink);white-space:nowrap}
.card-title{position:absolute;left:10px;top:44px;font-size:4px;font-style:italic;color:var(--accent);white-space:nowrap}
.card-contact{position:absolute;left:10px;top:57px;font-size:2.6px;line-height:4.2px;color:var(--ink-soft);white-space:nowrap}
.card-contact b{color:var(--accent);font-weight:600}
.card-address{position:absolute;right:9px;top:65px;font-size:2.6px;line-height:4.2px;color:var(--ink-soft);white-space:nowrap;text-align:right}

/* envelopes */
.envelope-front{left:798px;top:363px;width:328px;height:163px;background:var(--card-white)}
.envelope-front .lockup{position:absolute;left:22px;top:22px;font-size:6.5px;gap:5px}
.envelope-front .lockup .mark{width:8px;height:8px}
.envelope-back{left:800px;top:553px;width:328px;height:165px;background:var(--card-white)}
.envelope-back .flap{position:absolute;left:0;top:0;width:328px;height:62px}
.envelope-back .mark-small{position:absolute;left:159px;top:15px;width:10px;height:10px;background:#fff;opacity:.85}
.envelope-back .tagline{position:absolute;left:0;width:328px;top:40px;text-align:center;font-size:5px}
</style>
</head>
<body>

<section class="piece folder" aria-label="Presentation folder">
  <div class="lockup lockup--white"><span class="mark"></span><span>Tallow Reed<br>Software</span></div>
  <span class="mark-small"></span>
  <p class="tagline">See every device. Secure the network.</p>
</section>

<section class="piece letterhead" aria-label="Letterhead">
  <div class="lockup lockup--red"><span class="mark"></span><span>Tallow Reed<br>Software</span></div>
  <div class="letter-body">
    <p>Dear Client</p>
    <p>Thank you for meeting with our team last week. We are pleased to share a summary of the endpoint visibility review we discussed, along with next steps for your network security program.</p>
    <p>Our platform gives your IT department a clear view of every device that connects to the corporate network, so suspicious activity can be found and handled before it becomes a breach.</p>
    <p>We look forward to continuing the conversation and will follow up shortly to set a time for a full demonstration.</p>
    <p>Best regards,</p>
  </div>
  <div class="signature" role="img" aria-label="Handwritten signature of Dana Whitlock"></div>
  <div class="footer">
    <div class="col"><b>Address:</b> 4270 Vestridge Pond Blvd.,<br>Ste. 2600, Larkfield, WI 55812</div>
    <div class="col"><b>Office:</b> 555-0148-2290<br><b>Cell:</b> 555-0148-2291</div>
    <div class="col"><b>E-Mail:</b> contact@tallowreedsoftware.example<br><b>Web:</b> www.tallowreedsoftware.example</div>
  </div>
</section>

<section class="piece card card-front" aria-label="Business card front">
  <div class="lockup lockup--white"><span class="mark"></span><span>Tallow Reed<br>Software</span></div>
  <p class="tagline">See every device. Secure the network.</p>
</section>

<section class="piece card card-back" aria-label="Business card back">
  <div class="lockup lockup--red"><span class="mark"></span><span>Tallow Reed<br>Software</span></div>
  <p class="card-name">Dana Whitlock</p>
  <p class="card-title">Managing Director</p>
  <p class="card-contact"><b>Office:</b> 555-0148-2290<br><b>Cell:</b> 555-0148-2291<br>contact@tallowreedsoftware.example<br>www.tallowreedsoftware.example</p>
  <p class="card-address">4270 Vestridge Pond Blvd.,<br>Ste. 2600, Larkfield, WI 55812</p>
</section>

<section class="piece envelope-front" aria-label="Envelope front">
  <div class="lockup lockup--red"><span class="mark"></span><span>Tallow Reed<br>Software</span></div>
  <div class="footer">
    <div class="col"><b>Address:</b> 4270 Vestridge Pond Blvd.,<br>Ste. 2600, Larkfield, WI 55812</div>
    <div class="col"><b>Office:</b> 555-0148-2290<br><b>Cell:</b> 555-0148-2291</div>
    <div class="col"><b>E-Mail:</b> contact@tallowreedsoftware.example<br><b>Web:</b> www.tallowreedsoftware.example</div>
  </div>
</section>

<section class="piece envelope-back" aria-label="Envelope back">
  <svg class="flap" viewBox="0 0 328 62" aria-hidden="true">
    <path d="M0 0H328V58L164 62L0 58Z" fill="var(--brand-red)"/>
  </svg>
  <span class="mark-small"></span>
  <p class="tagline">See every device. Secure the network.</p>
</section>

</body>
</html>
```